Stylish Business Cards Wanted

- DOUBLE SIDED Design Required -

High end, edgy cards for a corporate and personal stylist. Must include logo,
Name: Belinda Harwick
Title: Director and Stylist
telephone : +61 8 7142 5809
email: belinda@theloombriefing.example
website: theloombriefing.example
Tag: Corporate Workwear & Uniform Specialist | Personal Stylist
Would like nice icons for telephone, email, website

Target Market(s)

Businesses wanting stylish uniforms, people wanting stylish wardrobes

Industry/Entity Type

Corporate Workwear Stylist

Contact Information for Business Card

I would like black, white and gold foiling incorporated in the design - possibly a touch of the other colours on my branding guide attached Name: Belinda Harwick Title: Director and Stylist telephone : +61 8 7142 5809 email: belinda@theloombriefing.example website: theloombriefing.example Tag: Corporate Workwear & Uniform Specialist | Personal Stylist Would like nice icons for telephone, email, website

Font styles to use
Other font styles liked:
• Raleway

Colors

Designer to choose colors to be used in the design.

Requirements
Must have
• Gold foil accents

```html
<!DOCTYPE html>
<html lang="en">
<head>
<meta charset="utf-8">
<title>The Loom Briefing — Business Cards</title>
<link href="https://fonts.googleapis.com/css2?family=Lato:wght@400;700&display=swap" rel="stylesheet">
<style>
  :root {
    --backdrop: #0c0c0c;
    --card: #262626;
    --card-edge: #c9a43a;
    --gold: #e0b43a;
    --white: #eceeed;
    --rule: #3b3b3b;
    --emboss: #3d3d3d;
  }
  * { margin: 0; padding: 0; box-sizing: border-box; }
  html, body {
    width: 1200px; height: 820px; overflow: hidden;
    background: var(--backdrop);
    font-family: "Lato", Arial, sans-serif;
  }
  .sheet {
    width: 1200px; height: 820px;
    display: flex; align-items: center; justify-content: center; gap: 40px;
  }
  .card {
    position: relative;
    width: 540px; height: 309px;
    background: var(--card);
    border: 1px solid var(--card-edge);
    overflow: hidden;
  }

  /* Front */
  .card-front .brand-name {
    position: absolute; top: 52px; right: 40px;
    color: var(--white); font-weight: 700; font-size: 30px;
    line-height: 1.1; text-align: right;
  }
  .card-front .brand-rule {
    position: absolute; top: 150px; left: 36px; right: 24px;
    height: 1px; background: var(--rule);
  }
  .identity { position: absolute; left: 36px; top: 168px; }
  .identity .person-name {
    color: var(--gold); font-weight: 700; font-size: 22px;
    text-transform: uppercase; letter-spacing: 0.2px;
  }
  .identity .person-title { color: var(--white); font-size: 15px; margin-top: 2px; }
  .identity .contact-rule { width: 150px; height: 1px; background: var(--rule); margin: 10px 0 10px; }
  .contact-list { list-style: none; }
  .contact-list li {
    display: flex; align-items: center; gap: 10px;
    color: var(--white); font-size: 13.5px; line-height: 21px;
  }
  .contact-list svg { width: 14px; height: 14px; flex: none; }

  /* Back */
  .card-back .brand-name {
    position: absolute; top: 70px; left: 0; right: 0;
    text-align: center;
    color: var(--emboss); font-weight: 700; font-size: 38px; line-height: 1.1;
  }
  .card-back .tagline {
    position: absolute; bottom: 34px; left: 0; right: 0;
    text-align: center; color: var(--white); font-size: 13px;
  }
  .tagline .dot { margin: 0 8px; }
</style>
</head>
<body>
<main class="sheet">

  <section class="card card-front" aria-label="Business card front">
    <div class="brand-name">The Loom<br>Briefing</div>
    <div class="brand-rule"></div>
    <div class="identity">
      <h1 class="person-name">Belinda Harwick</h1>
      <p class="person-title">Director and Stylist</p>
      <div class="contact-rule"></div>
      <ul class="contact-list">
        <li>
          <svg viewBox="0 0 16 16" aria-hidden="true"><path fill="var(--gold)" d="M3.6 1.2l2.3 2.6-1.2 1.6c.9 2 2.3 3.4 4.2 4.3l1.6-1.2 2.6 2.3-1.3 2.4C7 13.1 2.9 9 1.8 3.2z"/></svg>
          +61 8 7142 5809
        </li>
        <li>
          <svg viewBox="0 0 16 16" aria-hidden="true"><rect x="1" y="3.5" width="14" height="9" fill="var(--gold)"/><path d="M1.5 4l6.5 5 6.5-5" stroke="var(--card)" stroke-width="1.2" fill="none"/></svg>
          belinda@theloombriefing.example
        </li>
        <li>
          <svg viewBox="0 0 16 16" aria-hidden="true"><g fill="none" stroke="var(--gold)" stroke-width="1.3"><circle cx="8" cy="8" r="6.3"/><ellipse cx="8" cy="8" rx="2.8" ry="6.3"/><path d="M1.7 8h12.6M2.8 4.8h10.4M2.8 11.2h10.4"/></g></svg>
          theloombriefing.example
        </li>
      </ul>
    </div>
  </section>

  <section class="card card-back" aria-label="Business card back">
    <div class="brand-name">The Loom<br>Briefing</div>
    <p class="tagline">Corporate Workwear &amp; Uniform Specialist<span class="dot">•</span>Personal Stylist</p>
  </section>

</main>
</body>
</html>
```